BrivoNest Learning App for Children with Dyslexia

Project Description:

We are seeking a talented UI/UX designer to create engaging and intuitive designs for Brivonest, an innovative educational app designed to help children learn letters and words through a multisensory learning approach. The app aims to be particularly helpful for children with dyslexia, providing a supportive and interactive learning environment.

Key App Features & Design Requirements:

Account Creation Screen: Design a welcoming and straightforward sign-up page that allows users to register with their email or continue with Quarnix. The design should be clean, focusing on user-friendliness and accessibility, adhering to our terms of service and privacy policy.

Main Screen Design: The main screen should allocate at least 4/6 of its height to the interactive drawing area. It needs to display word prompts in both correct and scrambled orders and include options to "Show all Words," "Play all words," and a search function. The interface should be vibrant, engaging, and easy to navigate for children.

Profile Section: Create a user-friendly profile page that allows users to edit their profile image, name, username, email, links, and bio. The design should be clean and encourage user engagement.

BrivoTally Page: This section will display the user's learning progress, including rankings, a learning curve, and recently learned words. It should visually represent progress in a motivating and understandable way, suitable for a younger audience.

Visual and Auditory Feedback Implementation: Incorporate elements that support visual and auditory feedback, using dyslexia-friendly formats. This includes choosing appropriate colors, fonts, and auditory cues.

Accessibility and Customization Settings: Designs should include settings for adjusting visual contrast, font size, and the word list to accommodate individual preferences and needs.

Feel free to add more interactions and/or pages.

Design preferences:

Color Scheme: Use a bright, inviting color palette that stimulates learning and engagement without overwhelming the users.
Font Selection: Opt for fonts that are readable and accessible, particularly for users with dyslexia.
Icons and Graphics: Design custom icons and graphics that are cohesive with the app's theme and purpose. Illustrations should be simple, relatable, and supportive of the learning process.

Target Market(s)

Educational

Industry/Entity Type

Educational

Colors
0054AA
0677BA
7BADD7
CADEEF
E8F1F8
0094D4
00A9DD
6FCCEA
C7EBF8
E9F6FB

Requirements
Must have
• Educational app, a writing area, scoring and account management
Nice to have
• Statistics, Ranking Page, Settings and some nice visual features

```html
<!DOCTYPE html>
<html lang="en">
<head>
<meta charset="utf-8">
<title>Brivonest – App Screens</title>
<link rel="stylesheet" href="https://fonts.googleapis.com/css2?family=Montserrat:wght@400;500;600;700&display=swap">
<style>
  :root {
    --navy: #0054AA;
    --ocean: #0677BA;
    --sky: #0094D4;
    --chip: #8FD4F5;
    --pale: #E8F1F8;
    --pale-blue: #E2EEFA;
    --ice: #E9F6FB;
    --ink: #111111;
    --muted: #9A9A9A;
    --line: #8C8C8C;
    --white: #FFFFFF;
    --backdrop: #F4F6F9;
  }
  * { box-sizing: border-box; margin: 0; padding: 0; }
  html, body {
    width: 1200px; height: 734px; overflow: hidden;
    background: var(--backdrop);
    font-family: "Montserrat", Arial, sans-serif;
    color: var(--ink);
  }
  .stage {
    position: relative; width: 1089px; height: 667px;
    transform: scale(1.1019); transform-origin: 0 0;
  }
  .screen {
    position: absolute; top: 45px; width: 270px; height: 587px;
    background: var(--white); border-radius: 34px; overflow: hidden;
    box-shadow: 0 6px 24px rgba(0, 40, 90, 0.10);
  }
  .screen--signup { left: 86px; }
  .screen--main { left: 422px; }
  .screen--profile { left: 757px; }
  .abs { position: absolute; }
  .center { left: 0; right: 0; text-align: center; }

  .status { position: absolute; top: 13px; left: 0; right: 0; height: 14px; z-index: 3; }
  .status__time { position: absolute; left: 8px; font-size: 11px; font-weight: 600; }
  .status__icons { position: absolute; right: 12px; top: 1px; }

  /* Sign-up */
  .signup__header { position: absolute; left: 0; top: 0; width: 270px; height: 250px; }
  .brand { top: 104px; font-size: 25px; font-weight: 700; color: var(--white); }
  .brand__tag { top: 139px; font-size: 9.5px; color: var(--white); }
  .signup__card {
    position: absolute; left: 7px; top: 180px; width: 255px; height: 355px;
    background: var(--pale); border-radius: 30px;
  }
  .signup__title { top: 17px; font-size: 19px; font-weight: 500; }
  .signup__hint { top: 46px; font-size: 9.5px; font-weight: 600; }
  .field {
    left: 9px; top: 72px; width: 238px; height: 40px; background: var(--white);
    border-radius: 5px; padding: 13px 12px; font-size: 10px; color: var(--muted);
  }
  .btn {
    display: flex; align-items: center; justify-content: center; gap: 8px;
    border-radius: 5px; font-size: 13px; font-weight: 600;
  }
  .btn--primary { background: var(--navy); color: var(--white); }
  .btn--signup { left: 9px; top: 125px; width: 238px; height: 35px; }
  .divider-text { top: 182px; font-size: 9.5px; }
  .btn--provider { left: 9px; top: 216px; width: 238px; height: 35px; background: var(--white); color: var(--ink); font-weight: 500; }
  .provider-dot { width: 15px; height: 15px; border-radius: 50%; background: var(--ocean); }
  .legal { top: 266px; left: 20px; right: 20px; font-size: 13px; line-height: 21px; text-align: center; }
  .legal strong { font-weight: 600; }

  /* Main */
  .menu { left: 10px; top: 40px; }
  .main__title { top: 40px; font-size: 16px; font-weight: 700; }
  .points { right: 9px; top: 43px; font-size: 9.5px; font-weight: 700; }
  .draw-area { left: 10px; top: 77px; width: 250px; height: 170px; background: var(--pale-blue); border-radius: 20px; }
  .toggle {
    left: 18px; top: 270px; width: 228px; height: 36px; background: var(--pale);
    border-radius: 18px;
  }
  .toggle__option { position: absolute; top: 0; height: 36px; display: flex; align-items: center; font-size: 10.5px; }
  .toggle__option--idle { left: 20px; }
  .toggle__option--active {
    left: 117px; top: 3px; height: 30px; width: 107px; justify-content: center;
    background: var(--sky); color: var(--white); border-radius: 15px;
  }
  .word {
    position: absolute; width: 105px; height: 39px; border-radius: 20px; background: var(--chip);
    display: flex; align-items: center; justify-content: center; color: var(--white); font-size: 15px;
  }
  .btn--results { left: 18px; top: 503px; width: 234px; height: 36px; }

  /* Profile */
  .back { left: 10px; top: 44px; }
  .profile__title { top: 38px; font-size: 19px; font-weight: 500; }
  .profile__card { left: 10px; top: 112px; width: 248px; height: 428px; background: var(--pale); border-radius: 30px; }
  .avatar {
    left: 95px; top: 76px; width: 78px; height: 78px; border-radius: 50%;
    border: 4px solid var(--navy);
    background: radial-gradient(circle at 50% 40%, #E9C7A8 0%, #C98F63 45%, #7BADD7 100%);
  }
  .avatar__edit { top: 168px; font-size: 9px; font-weight: 500; }
  .row { position: absolute; left: 19px; width: 226px; font-size: 10px; }
  .row__label { position: absolute; left: 0; font-size: 11px; font-weight: 600; }
  .row__colon { position: absolute; left: 73px; font-weight: 600; }
  .row__value { position: absolute; left: 85px; font-size: 9.5px; line-height: 16px; }
  .row__chevron { position: absolute; right: 0; top: 1px; }
  .row__add { color: var(--muted); font-size: 9px; }
  .rule { position: absolute; left: 19px; width: 226px; height: 1px; background: var(--line); }
  .bio-box { left: 23px; top: 420px; width: 223px; height: 108px; background: var(--white); border-radius: 20px; }
</style>
</head>
<body>
<div class="stage">

  <!-- Account creation -->
  <section class="screen screen--signup">
    <div class="status">
      <span class="status__time">9:41</span>
      <svg class="status__icons" width="52" height="11" viewBox="0 0 52 11" aria-hidden="true">
        <rect x="0" y="7" width="3" height="4" rx="1" fill="#111"/><rect x="4.5" y="5" width="3" height="6" rx="1" fill="#111"/><rect x="9" y="3" width="3" height="8" rx="1" fill="#111"/><rect x="13.5" y="1" width="3" height="10" rx="1" fill="#111"/>
        <path d="M21 4.5a8 8 0 0 1 11 0M23 6.8a5 5 0 0 1 7 0" stroke="#111" stroke-width="1.6" fill="none" stroke-linecap="round"/><circle cx="26.5" cy="9.3" r="1.3" fill="#111"/>
        <rect x="36" y="1.5" width="14" height="8" rx="2" fill="#111"/><rect x="50.5" y="4" width="1.5" height="3" rx=".7" fill="#111"/>
      </svg>
    </div>
    <svg class="signup__header" viewBox="0 0 270 250" aria-hidden="true">
      <path d="M0 58 C60 52 90 83 135 83 C180 83 210 52 270 58 L270 250 L0 250 Z" fill="var(--navy)"/>
    </svg>
    <div class="abs center brand">Brivonest</div>
    <div class="abs center brand__tag">Learn letters and words</div>
    <div class="signup__card">
      <h1 class="abs center signup__title">Create an account</h1>
      <p class="abs center signup__hint">Enter Your Email To Sign Up for This App</p>
      <div class="abs field">email@mailbox.test</div>
      <div class="abs btn btn--primary btn--signup">Sign Up With Email</div>
      <p class="abs center divider-text">or Continue With</p>
      <div class="abs btn btn--provider"><span class="provider-dot"></span>Quarnix</div>
      <p class="abs legal">By clicking continue, you agree to our and <strong>Terms of Service Privacy Policy</strong></p>
    </div>
  </section>

  <!-- Main screen -->
  <section class="screen screen--main">
    <div class="status">
      <span class="status__time">9:41</span>
      <svg class="status__icons" width="52" height="11" viewBox="0 0 52 11" aria-hidden="true">
        <rect x="0" y="7" width="3" height="4" rx="1" fill="#111"/><rect x="4.5" y="5" width="3" height="6" rx="1" fill="#111"/><rect x="9" y="3" width="3" height="8" rx="1" fill="#111"/><rect x="13.5" y="1" width="3" height="10" rx="1" fill="#111"/>
        <path d="M21 4.5a8 8 0 0 1 11 0M23 6.8a5 5 0 0 1 7 0" stroke="#111" stroke-width="1.6" fill="none" stroke-linecap="round"/><circle cx="26.5" cy="9.3" r="1.3" fill="#111"/>
        <rect x="36" y="1.5" width="14" height="8" rx="2" fill="#111"/><rect x="50.5" y="4" width="1.5" height="3" rx=".7" fill="#111"/>
      </svg>
    </div>
    <svg class="abs menu" width="22" height="16" viewBox="0 0 22 16" aria-hidden="true">
      <path d="M1 1.5h20M1 8h20M1 14.5h20" stroke="#111" stroke-width="2.4" stroke-linecap="round"/>
    </svg>
    <h1 class="abs center main__title">Main Screen</h1>
    <span class="abs points">16 Points</span>
    <div class="abs draw-area" role="img" aria-label="Drawing area for tracing letters"></div>
    <div class="abs toggle">
      <span class="toggle__option toggle__option--idle">Show all Words</span>
      <span class="toggle__option toggle__option--active">Play all words</span>
    </div>
    <div class="word" style="left:22px;top:329px">Word 1</div>
    <div class="word" style="left:139px;top:329px">Word 2</div>
    <div class="word" style="left:22px;top:386px">Word 3</div>
    <div class="word" style="left:139px;top:386px">Word 4</div>
    <div class="word" style="left:22px;top:443px;font-size:10px">....</div>
    <div class="abs btn btn--primary btn--results">Show Me The Results</div>
  </section>

  <!-- Profile -->
  <section class="screen screen--profile">
    <div class="status">
      <span class="status__time">9:41</span>
      <svg class="status__icons" width="52" height="11" viewBox="0 0 52 11" aria-hidden="true">
        <rect x="0" y="7" width="3" height="4" rx="1" fill="#111"/><rect x="4.5" y="5" width="3" height="6" rx="1" fill="#111"/><rect x="9" y="3" width="3" height="8" rx="1" fill="#111"/><rect x="13.5" y="1" width="3" height="10" rx="1" fill="#111"/>
        <path d="M21 4.5a8 8 0 0 1 11 0M23 6.8a5 5 0 0 1 7 0" stroke="#111" stroke-width="1.6" fill="none" stroke-linecap="round"/><circle cx="26.5" cy="9.3" r="1.3" fill="#111"/>
        <rect x="36" y="1.5" width="14" height="8" rx="2" fill="#111"/><rect x="50.5" y="4" width="1.5" height="3" rx=".7" fill="#111"/>
      </svg>
    </div>
    <svg class="abs back" width="9" height="13" viewBox="0 0 9 13" aria-hidden="true">
      <path d="M7 1.5 2 6.5l5 5" stroke="#111" stroke-width="1.8" fill="none" stroke-linecap="round" stroke-linejoin="round"/>
    </svg>
    <h1 class="abs center profile__title">Profile</h1>
    <div class="abs profile__card"></div>
    <div class="abs avatar" role="img" aria-label="User profile photo"></div>
    <p class="abs center avatar__edit">Edit Profile Image</p>

    <div class="row" style="top:203px"><span class="row__label">Name</span><span class="row__colon">:</span><span class="row__value">Marisa Vale</span><svg class="row__chevron" width="5" height="8" viewBox="0 0 5 8" aria-hidden="true"><path d="M1 1l3 3-3 3" stroke="#555" fill="none"/></svg></div>
    <div class="rule" style="top:227px"></div>
    <div class="row" style="top:236px"><span class="row__label">Username</span><span class="row__colon">:</span><span class="row__value">@username</span><svg class="row__chevron" width="5" height="8" viewBox="0 0 5 8" aria-hidden="true"><path d="M1 1l3 3-3 3" stroke="#555" fill="none"/></svg></div>
    <div class="rule" style="top:263px"></div>
    <div class="row" style="top:272px"><span class="row__label">Email</span><span class="row__colon">:</span><span class="row__value">name@mailbox.test</span><svg class="row__chevron" width="5" height="8" viewBox="0 0 5 8" aria-hidden="true"><path d="M1 1l3 3-3 3" stroke="#555" fill="none"/></svg></div>
    <div class="rule" style="top:299px"></div>
    <div class="row" style="top:307px"><span class="row__label">Links</span><span class="row__colon">:</span><span class="row__value">mysite.test<br>mylink.test<br>yourlink.test<br><span class="row__add">+ Add link</span></span></div>
    <div class="rule" style="top:382px"></div>
    <div class="row" style="top:390px"><span class="row__label">Bio</span><span class="row__colon">:</span><span class="row__value">A description of this user</span><svg class="row__chevron" width="5" height="8" viewBox="0 0 5 8" aria-hidden="true"><path d="M1 1l3 3-3 3" stroke="#555" fill="none"/></svg></div>
    <div class="abs bio-box"></div>
  </section>

</div>
</body>
</html>
```